K7 Construction Site Sign

I would like to get a sign designed which would be installed at a construction sign. I would like to incorporate my current logo, font and colors in the sign. The sign would be 30" x 60" (vertical). Would like to keep it clean and simple yet eye catching and sparks interest. I have attached my branding colors. I would like the background to be the branded blue with white text.

```html
<!DOCTYPE html>
<html lang="en">
<head>
<meta charset="utf-8">
<title>K7 Construction Site Sign</title>
<link rel="stylesheet" href="https://fonts.googleapis.com/css2?family=Nunito:wght@400&display=swap">
<style>
  :root {
    --brand-blue: #2a527f;
    --brand-orange: #f9b042;
    --white: #ffffff;
    --page: #ffffff;
  }
  * { margin: 0; padding: 0; box-sizing: border-box; }
  html, body {
    width: 1200px;
    height: 829px;
    overflow: hidden;
    background: var(--page);
  }
  .canvas {
    position: relative;
    width: 1200px;
    height: 829px;
    display: flex;
    align-items: center;
    justify-content: center;
  }
  .site-sign {
    width: 347px;
    height: 693px;
    display: flex;
    flex-direction: column;
    box-shadow: 2px 3px 6px rgba(0, 0, 0, 0.35);
    font-family: "Nunito", sans-serif;
    color: var(--white);
  }
  .sign-top {
    height: 360px;
    background: var(--brand-blue);
    display: flex;
    align-items: flex-start;
    justify-content: center;
    padding-top: 62px;
  }
  .brand-name {
    font-size: 170px;
    font-weight: 400;
    line-height: 1;
    letter-spacing: -4px;
    color: var(--white);
  }
  .divider {
    height: 22px;
    background: var(--white);
  }
  .sign-bottom {
    flex: 1;
    background: var(--brand-orange);
    padding: 117px 0 0 36px;
  }
  .tagline {
    font-size: 29px;
    font-weight: 400;
    line-height: 35px;
    letter-spacing: 0.2px;
    text-transform: uppercase;
    white-space: nowrap;
  }
</style>
</head>
<body>
  <main class="canvas">
    <article class="site-sign">
      <section class="sign-top">
        <span class="brand-name">K7</span>
      </section>
      <div class="divider"></div>
      <section class="sign-bottom">
        <p class="tagline">Contracting &amp;<br>Development Ltd.</p>
      </section>
    </article>
  </main>
</body>
</html>
```